Business Card Design Project

I need a business card designed from scratch. I have an existing logo that I can upload in Illustrator for modification or redesign.

The Company is called Query Lanterns http://querylanterns.com.au and we provide Search Engine Optimization services to Australian businesses. The current logo signifies an increase in visitors, profits etc...

There are no restrictions as to the redesign - colours, style etc are all open to change.

Cards will be full colour and one sided printed at http://www.cardmoxel.com.au so check their requirements for file format and sizes etc.

I will expect all original files upon completion of project.

Target Market(s)

Any business with a web site looking to improve their search engine rankings

Industry/Entity Type

Business

Requirements
Must have
• I like modern, sleek designs. Clean, not fussy, uncluttered.

```html
<!DOCTYPE html>
<html lang="en">
<head>
<meta charset="utf-8">
<title>Query Lanterns – Business Card</title>
<link rel="stylesheet" href="https://fonts.googleapis.com/css2?family=Delius&display=swap">
<style>
  :root {
    --paper-light: #eeecd2;
    --paper-mid: #e2dfc0;
    --paper-shade: #cfcaa6;
    --ink-blue: #1f7fc6;
    --ink-dark: #1d3140;
    --ornament: 79, 75, 63;
    --gold: 214, 168, 62;
  }
  html, body {
    margin: 0;
    padding: 0;
    width: 1200px;
    height: 687px;
    overflow: hidden;
    background: #ffffff;
  }
  .card {
    position: relative;
    width: 1200px;
    height: 687px;
    overflow: hidden;
    font-family: "Delius", cursive;
    color: var(--ink-dark);
    background:
      radial-gradient(ellipse at 30% 40%, rgba(255,255,245,0.55), transparent 55%),
      radial-gradient(ellipse at 75% 70%, rgba(190,180,150,0.35), transparent 60%),
      radial-gradient(ellipse at 55% 15%, rgba(200,205,170,0.4), transparent 50%),
      linear-gradient(135deg, var(--paper-light) 0%, var(--paper-mid) 55%, var(--paper-shade) 100%);
  }
  .ornament-top-right {
    position: absolute;
    right: 0;
    top: 0;
    width: 470px;
    height: 390px;
    background: radial-gradient(ellipse at 100% 0%, rgba(var(--ornament),0.5) 0%, rgba(var(--ornament),0.22) 45%, transparent 72%);
  }
  .ornament-bottom-left {
    position: absolute;
    left: 0;
    bottom: 0;
    width: 340px;
    height: 270px;
    background: radial-gradient(ellipse at 0% 100%, rgba(var(--ornament),0.5) 0%, rgba(var(--ornament),0.22) 45%, transparent 72%);
  }
  .mascot-illustration {
    position: absolute;
    left: 0;
    top: 150px;
    width: 230px;
    height: 300px;
    background: radial-gradient(ellipse 50% 50% at 50% 50%, rgba(var(--gold),0.55) 0%, rgba(var(--gold),0.28) 50%, rgba(var(--gold),0) 100%);
  }
  .brand {
    position: absolute;
    left: 30px;
    top: 66px;
    display: flex;
    align-items: center;
    gap: 12px;
  }
  .brand-mark {
    width: 22px;
    height: 22px;
    border-radius: 50%;
    background: var(--ink-blue);
  }
  .brand-name {
    font-size: 42px;
    line-height: 1;
    color: var(--ink-blue);
    white-space: nowrap;
  }
  .identity {
    position: absolute;
    left: 0;
    right: 0;
    top: 206px;
    text-align: center;
  }
  .full-name {
    margin: 0;
    font-size: 48px;
    font-weight: 400;
    color: var(--ink-blue);
    text-shadow: 0 0 6px rgba(240,180,70,0.7);
    line-height: 1.1;
  }
  .company-message {
    margin: 16px 0 0;
    font-size: 28px;
    color: var(--ink-dark);
  }
  .contact,
  .address {
    position: absolute;
    margin: 0;
    font-size: 29px;
    color: var(--ink-dark);
    font-style: normal;
  }
  .contact { left: 251px; top: 436px; line-height: 32px; }
  .address { left: 759px; top: 428px; line-height: 39px; }
</style>
</head>
<body>
  <div class="card">
    <div class="ornament-top-right" role="img" aria-label="Floral scroll ornament in dark grey"></div>
    <div class="ornament-bottom-left" role="img" aria-label="Floral scroll ornament in dark grey"></div>
    <div class="mascot-illustration" role="img" aria-label="Gold figure holding a magnifying glass"></div>

    <div class="brand">
      <span class="brand-mark"></span>
      <span class="brand-name">Query Lanterns</span>
    </div>

    <div class="identity">
      <h1 class="full-name">full name</h1>
      <p class="company-message">Company message</p>
    </div>

    <p class="contact">Phone / other<br>Fax / other<br>email / other</p>
    <address class="address">address line 1<br>address line 2<br>address line 3</address>
  </div>
</body>
</html>
```